Business card for Luxury Portable Restroom Trailer company

We are a Luxury Portable Restroom Trailer Company Called FALCRIDGE HIRES. Based in Orange County California. We provide portable restroom trailers for events, such as, Weddings, Concerts, Charity events, Sporting events, Tournaments, Corporate events, ect. We rent and Sell the Luxury restrooms. Our colors are white, grey, and Orange. As you will see in the logo we uploaded.
There are 2 people in the company so the names and titles will change for the 3 people but card will remain the same. Here is the information for each Person: Dwight Penner CFO 555 318-0476
next Person: Leon Marchetti VP 555 318-0476
Next Person: Owen Marchetti CEO 555 318-0476
Information to include on the card: Luxury Restroom Trailers Rental and Sales. Weddings, Concerts, Charity, Sporting and Corp. Events.

```html
<!DOCTYPE html>
<html lang="en">
<head>
<meta charset="utf-8">
<title>Falcridge Hires – Business Card</title>
<link href="https://fonts.googleapis.com/css2?family=Arimo:wght@400;700&display=swap" rel="stylesheet">
<style>
  :root {
    --stage: #3a3436;
    --card: #f6f6f7;
    --grey: #5b5b5d;
    --ink: #2a2a2c;
    --orange: #ee5a1e;
  }
  * { margin: 0; padding: 0; box-sizing: border-box; }
  html, body {
    width: 1200px;
    height: 1108px;
    overflow: hidden;
    background: var(--stage);
    font-family: "Arimo", Arial, sans-serif;
  }
  .card {
    position: absolute;
    left: 220px;
    width: 760px;
    height: 434px;
    background: var(--card);
    border-radius: 28px;
    box-shadow: 0 14px 30px rgba(0,0,0,.35);
  }
  .card--front { top: 70px; }
  .card--back { top: 604px; }

  .wordmark {
    display: flex;
    align-items: center;
    gap: 14px;
  }
  .wordmark__square {
    width: 22px;
    height: 22px;
    background: var(--orange);
  }
  .wordmark__name {
    font-weight: 700;
    color: var(--grey);
    letter-spacing: 1px;
    white-space: nowrap;
  }

  .card--front .wordmark {
    position: absolute;
    left: 130px;
    top: 120px;
  }
  .card--front .wordmark__name { font-size: 50px; }
  .card--front .wordmark__square { width: 36px; height: 36px; }

  .tagline {
    position: absolute;
    left: 130px;
    top: 232px;
    font-size: 19px;
    line-height: 1.45;
    color: var(--grey);
  }

  .card--back .wordmark {
    position: absolute;
    right: 54px;
    top: 92px;
  }
  .card--back .wordmark__name { font-size: 26px; }

  .person {
    position: absolute;
    left: 58px;
    top: 150px;
  }
  .person__name {
    font-size: 27px;
    font-weight: 700;
    color: var(--orange);
    text-transform: uppercase;
    letter-spacing: .5px;
  }
  .person__title {
    font-size: 18px;
    color: var(--grey);
    margin-top: 2px;
  }
  .address {
    position: absolute;
    left: 58px;
    top: 232px;
    font-size: 19px;
    line-height: 1.35;
    color: var(--ink);
  }
  .web {
    position: absolute;
    left: 58px;
    top: 312px;
    font-size: 19px;
    letter-spacing: 4px;
    color: var(--ink);
  }
  .contact {
    position: absolute;
    left: 340px;
    top: 258px;
    font-size: 20px;
    line-height: 1.35;
    color: var(--ink);
  }
</style>
</head>
<body>
  <section class="card card--front">
    <div class="wordmark">
      <span class="wordmark__square"></span>
      <span class="wordmark__name">FALCRIDGE HIRES</span>
    </div>
    <p class="tagline">
      Luxury Restroom Trailers Rental and Sales<br>
      Weddings, Concerts, Charity, Sporting and Corp Events
    </p>
  </section>

  <section class="card card--back">
    <div class="person">
      <p class="person__name">Dwight Penner</p>
      <p class="person__title">CFO</p>
    </div>
    <p class="address">2716 Harbor Crest Drive<br>Tustin, CA 92780</p>
    <p class="web">www.FALCRIDGE.com</p>
    <p class="contact">555 318-0476<br>name@FALCRIDGE.com</p>
    <div class="wordmark">
      <span class="wordmark__square"></span>
      <span class="wordmark__name">FALCRIDGE HIRES</span>
    </div>
  </section>
</body>
</html>
```